Ward Compass Business Card Design*

We need a business card design for our company Ward Compass. Our company is specialized in providing online consulting services regarding medical institutions, hospitals and doctors. We work with patients worldwide looking to choose between healthcare providers. We have a website you may use as a reference, where we list doctors and clinics worldwide. So we target Medical providers as well as patients worldwide.
Target Market(s)
Medical Providers and patients around the world
Industry/Entity Type
Medical
Contact Information for Business Card
Salwa Kettani
CEO
+90 612 348 2175
info@wardcompass.example
www.wardcompass.example
14 Annakhil 7 H.R.B. Rabat, Morocco
Requirements
Must have
- Company logo/name on one full side, personal info and smaller logo and company name on the other side.
Nice to have
- Smart and elegant design

```html
<!DOCTYPE html>
<html lang="en">
<head>
<meta charset="utf-8">
<title>Ward Compass Business Card</title>
<link href="https://fonts.googleapis.com/css2?family=Lato:wght@400;700&display=swap" rel="stylesheet">
<style>
  :root {
    --backdrop: #d6d6d6;
    --brand-blue: #2e77b5;
    --accent-blue: #34a5d8;
    --paper: #ffffff;
    --ink-light: #ffffff;
  }
  * { margin: 0; padding: 0; box-sizing: border-box; }
  html, body {
    width: 1200px;
    height: 802px;
    overflow: hidden;
    background: var(--backdrop);
    font-family: "Lato", sans-serif;
  }
  .stage { position: relative; width: 1200px; height: 802px; }
  .card {
    position: absolute;
    top: 274px;
    width: 442px;
    height: 265px;
    overflow: hidden;
  }
  .card-front { left: 136px; background: var(--brand-blue); color: var(--ink-light); }
  .card-back { left: 624px; background: var(--paper); }

  .front-disc {
    position: absolute;
    left: 216px; top: -3px;
    width: 268px; height: 268px;
    border-radius: 50%;
    background: var(--accent-blue);
  }
  .front-brand {
    position: absolute;
    left: 21px; top: 226px;
    font-weight: 700; font-size: 13px; letter-spacing: 0.4px;
    color: var(--ink-light); text-transform: uppercase;
  }

  .person { position: absolute; left: 21px; top: 83px; }
  .person-name { font-size: 15.5px; letter-spacing: 0.2px; line-height: 1; }
  .person-name .first { font-weight: 700; }
  .person-name .last { font-weight: 400; }
  .person-role { font-size: 12px; line-height: 1; margin-top: 2px; }

  .contacts { position: absolute; left: 21px; top: 143px; list-style: none; }
  .contacts li {
    display: flex; align-items: center; gap: 3px;
    font-size: 12.5px; line-height: 16px; height: 16px;
  }
  .contacts svg { width: 11px; height: 11px; flex: none; fill: var(--ink-light); }

  .brand {
    position: absolute; left: 97px; top: 102px;
    display: flex; align-items: center; gap: 14px;
  }
  .brand-dot { width: 58px; height: 58px; border-radius: 50%; background: var(--brand-blue); }
  .brand-name {
    font-weight: 700; font-size: 23px; letter-spacing: 0.3px;
    color: var(--brand-blue); text-transform: uppercase;
  }
</style>
</head>
<body>
<main class="stage">
  <section class="card card-front" aria-label="Business card, personal side">
    <span class="front-disc" aria-hidden="true"></span>
    <div class="person">
      <p class="person-name"><span class="first">SALWA</span> <span class="last">KETTANI</span></p>
      <p class="person-role">CEO</p>
    </div>
    <ul class="contacts">
      <li>
        <svg viewBox="0 0 12 12" aria-hidden="true"><path d="M1 3.5C1 2 2.5 1.5 6 1.5S11 2 11 3.5v1H8.5v-1h-5v1H1z"/><path d="M2.5 6h7l1 4.5h-9z"/></svg>
        <span>+90 612 348 2175</span>
      </li>
      <li>
        <svg viewBox="0 0 12 12" aria-hidden="true"><path d="M1 2.5h10v7H1z M1.8 3.3 6 6.5l4.2-3.2" stroke="#2e77b5" stroke-width="0.8"/></svg>
        <span>info@wardcompass.example</span>
      </li>
      <li>
        <svg viewBox="0 0 12 12" aria-hidden="true"><circle cx="6" cy="6" r="5"/><path d="M3 4.5h3v2H4zM7 7.5h2l-1 2z" fill="#2e77b5"/></svg>
        <span>www.wardcompass.example</span>
      </li>
    </ul>
    <p class="front-brand">Ward Compass</p>
  </section>

  <section class="card card-back" aria-label="Business card, brand side">
    <div class="brand">
      <span class="brand-dot" aria-hidden="true"></span>
      <span class="brand-name">Ward Compass</span>
    </div>
  </section>
</main>
</body>
</html>
```